Estate Planning Law Firm opening new branch in Florida

I am an experienced estate planning attorney that recently relocated to Florida. Looking for a banner Ad to place on platforms such as HomeLane, Chatterbox and Picturely to create publicity for firm and new leads.

```html
<!DOCTYPE html>
<html lang="en">
<head>
<meta charset="utf-8">
<title>Calderra Law Firm – Estate Planning Banner</title>
<link rel="stylesheet" href="https://fonts.googleapis.com/css2?family=PT+Serif:wght@700&family=Open+Sans:wght@600&display=swap">
<style>
  :root {
    --white: #ffffff;
    --teal: #2b7b7d;
    --foliage-dark: #2e3a1c;
    --foliage: #5d6b2c;
    --foliage-light: #8a8d3a;
    --concrete: #5a5a55;
    --concrete-light: #8c8a80;
    --overhang: #26292b;
    --lawn: #6f7a3a;
  }
  * { margin: 0; padding: 0; box-sizing: border-box; }
  html, body { width: 1200px; height: 628px; overflow: hidden; background: var(--white); }
  .banner {
    position: relative;
    width: 1200px;
    height: 628px;
    overflow: hidden;
  }
  .hero-photo {
    position: absolute;
    inset: 0;
    background:
      linear-gradient(180deg, var(--overhang) 0%, var(--overhang) 20%, transparent 32%),
      radial-gradient(ellipse 260px 420px at 1130px 340px, var(--foliage-light) 0%, transparent 70%),
      linear-gradient(180deg, transparent 80%, var(--lawn) 100%),
      linear-gradient(90deg, var(--foliage-dark) 0%, var(--foliage) 22%, var(--concrete) 45%, var(--concrete-light) 65%, var(--concrete) 82%, var(--foliage) 100%);
  }
  .hero-shade {
    position: absolute;
    inset: 0;
    background: linear-gradient(90deg, rgba(20,24,12,0.55) 0%, rgba(20,24,12,0.25) 40%, rgba(0,0,0,0) 60%);
  }
  .brand {
    position: absolute;
    left: 78px;
    top: 70px;
    display: flex;
    align-items: flex-start;
    gap: 14px;
    color: var(--white);
  }
  .brand-mark {
    width: 52px;
    height: 52px;
    margin-top: 6px;
    background: var(--white);
  }
  .brand-text { display: flex; flex-direction: column; align-items: center; }
  .brand-name {
    font-family: "PT Serif", Georgia, serif;
    font-weight: 700;
    font-size: 52px;
    line-height: 52px;
    letter-spacing: 1px;
  }
  .brand-sub {
    display: flex;
    align-items: center;
    gap: 8px;
    margin-top: 6px;
    font-family: "PT Serif", Georgia, serif;
    font-weight: 700;
    font-size: 15px;
    letter-spacing: 1px;
  }
  .brand-sub::before, .brand-sub::after {
    content: "";
    width: 64px;
    height: 1.5px;
    background: var(--white);
  }
  .headline {
    position: absolute;
    left: 78px;
    top: 240px;
    font-family: "PT Serif", Georgia, serif;
    font-weight: 700;
    color: var(--white);
    text-transform: uppercase;
    text-shadow: 0 2px 8px rgba(0,0,0,0.25);
  }
  .headline-lead { display: block; font-size: 72px; line-height: 86px; }
  .headline-line { display: block; font-size: 58px; line-height: 68px; }
  .tag {
    position: absolute;
    left: 0;
    top: 488px;
    width: 363px;
    height: 70px;
    padding-left: 42px;
    display: flex;
    align-items: center;
    background: var(--teal);
    border-radius: 0 35px 35px 0;
    font-family: "Open Sans", Arial, sans-serif;
    font-weight: 600;
    font-size: 20px;
    color: var(--white);
    text-transform: uppercase;
  }
</style>
</head>
<body>
  <main class="banner">
    <div class="hero-photo" role="img" aria-label="Photo: an attorney holding a folder shows a young family a modern concrete home surrounded by trees"></div>
    <div class="hero-shade"></div>

    <div class="brand">
      <span class="brand-mark"></span>
      <div class="brand-text">
        <span class="brand-name">CALDERRA</span>
        <span class="brand-sub">LAW FIRM, PLLC</span>
      </div>
    </div>

    <h1 class="headline">
      <span class="headline-lead">Experienced</span>
      <span class="headline-line">Estate Planning</span>
      <span class="headline-line">Law Firm.</span>
    </h1>

    <div class="tag">Relocated to Florida</div>
  </main>
</body>
</html>
```